Health and wellnes company needs business cards

We are a Health and wellness business just relocated to Spain. Here nobody knows our business so we would like to put some of our services on the card. Clean design with logo.

Contact Information for Business Card

Brightmeadow
Paula & Oskar Dunbeck
Calle del Almendro 57
Sanlúcar de Barrameda
Mobile: 0046 731 402687
info@brightmeadow.example

Font styles to use
Serif

Colors
85cae6
85acd3
b768aa

Requirements
Must have
• these Services somewhere on the card
• - Private or group yoga
• - Reconnective healing
• - Kitesurfing lessons
• - Massage
• LOgo somewhere
Nice to have
• Colours that go with the logo please

```html
<!DOCTYPE html>
<html lang="en">
<head>
<meta charset="utf-8">
<title>Brightmeadow business card</title>
<link rel="stylesheet" href="https://fonts.googleapis.com/css2?family=Marcellus&family=Philosopher:wght@700&family=Lexend:wght@300;400&display=swap">
<style>
  :root {
    --navy-top: #2a4d73;
    --navy: #1a365f;
    --teal: #75c9c9;
    --white: #ffffff;
    --backdrop: #e4e4e4;
  }
  * { box-sizing: border-box; margin: 0; padding: 0; }
  html, body { width: 1200px; height: 1200px; overflow: hidden; }
  body { background: var(--backdrop); position: relative; font-family: "Lexend", sans-serif; }

  .card {
    position: absolute;
    left: 262px;
    width: 686px;
    height: 392px;
    border-radius: 24px;
    overflow: hidden;
  }
  .card--front { top: 165px; background: linear-gradient(var(--navy-top), var(--navy)); }
  .card--back { top: 653px; background: var(--white); }

  .holders {
    position: absolute; left: 34px; top: 106px;
    font-family: "Philosopher", serif; font-weight: 700;
    font-size: 19px; color: var(--teal);
  }
  .address {
    position: absolute; left: 34px; top: 150px;
    font-weight: 300; font-size: 16px; line-height: 19.5px; color: var(--white);
  }
  .contacts {
    position: absolute; left: 34px; top: 222px; list-style: none;
    font-weight: 300; font-size: 16px; line-height: 20px; color: var(--white);
  }
  .contacts li { display: flex; align-items: center; gap: 8px; }
  .contacts svg { width: 13px; height: 13px; flex: none; }

  .front-emblem {
    position: absolute; left: 272px; top: -2px;
    width: 394px; height: 394px; border-radius: 50%;
    background: var(--white); border: 14px solid var(--teal);
  }

  .back-mark {
    position: absolute; left: 279px; top: 98px;
    width: 126px; height: 126px; border-radius: 50%;
    border: 9px solid var(--teal);
  }
  .brand {
    position: absolute; left: 0; right: 0; top: 230px; text-align: center;
    font-family: "Marcellus", serif; font-size: 44px; letter-spacing: 0.5px;
    color: var(--navy);
  }
  .services {
    position: absolute; left: 0; right: 0; top: 336px;
    display: flex; justify-content: center; align-items: center; gap: 7px;
    list-style: none; font-size: 16px; color: var(--navy);
  }
  .services li + li::before {
    content: ""; display: inline-block; width: 5px; height: 5px; border-radius: 50%;
    background: var(--teal); margin-right: 7px; vertical-align: middle;
  }
</style>
</head>
<body>
  <section class="card card--front">
    <h1 class="holders">Paula &amp; Oskar Dunbeck</h1>
    <p class="address">Calle del Almendro 57<br>Sanlúcar<br>de Barrameda</p>
    <ul class="contacts">
      <li>
        <svg viewBox="0 0 13 13"><rect x="3" y="0.5" width="7" height="12" rx="1.5" fill="none" stroke="#75c9c9" stroke-width="1.4"/><rect x="5" y="10" width="3" height="1" fill="#75c9c9"/></svg>
        0046 731 402687
      </li>
      <li>
        <svg viewBox="0 0 13 13"><rect x="0.5" y="3" width="12" height="8" fill="#75c9c9"/><path d="M0.5 3 L6.5 7.5 L12.5 3" fill="none" stroke="#1a365f" stroke-width="1"/></svg>
        info@brightmeadow.example
      </li>
      <li>
        <svg viewBox="0 0 13 13"><circle cx="6.5" cy="6.5" r="6" fill="#75c9c9"/><path d="M3 4 q2 1 2 3 q0 2 2 3 M8 2 q2 2 3 2" fill="none" stroke="#1a365f" stroke-width="1.2"/></svg>
        www.brightmeadow.example
      </li>
    </ul>
    <div class="front-emblem" aria-hidden="true"></div>
  </section>

  <section class="card card--back">
    <div class="back-mark" aria-hidden="true"></div>
    <p class="brand">BRIGHTMEADOW</p>
    <ul class="services">
      <li>Private or group yoga</li>
      <li>Reconnective healing</li>
      <li>Kitesurfing lessons</li>
      <li>Massage</li>
    </ul>
  </section>
</body>
</html>
```